Design a compelling Tarnwove Business Card that will drive people to my site

I want a business card that I can give to people—less to tell them who I am and more to direct them to my website. My website is a portal for Pelmor Aquatics Officials and a place for people who want to become Pelmor Aquatics Officials.
I am uploading my official company logo as well as a business card mockup that I did on my own. Please feel free to completely stray from this design.
I've included a screen recording of the homepage of my website as well.
Target Market(s)
Pelmor Aquatics Officials and people who desire to become one
Contact Information for Business Card
website url
Look and feel
Each slider illustrates characteristics of the customer's brand and the style your logo design should communicate.

```html
<!DOCTYPE html>
<html lang="en">
<head>
<meta charset="utf-8">
<title>Tarnwove Business Card</title>
<link rel="stylesheet" href="https://fonts.googleapis.com/css2?family=Montserrat:wght@400;500;700&display=swap">
<style>
  :root {
    --brand-blue: #3a55a8;
    --soft-blue: #9aaddc;
    --paper: #ffffff;
    --backdrop: #e9eaee;
    --text-light: #ffffff;
  }
  * { margin: 0; padding: 0; box-sizing: border-box; }
  html, body {
    width: 1200px; height: 912px; overflow: hidden;
    background: var(--backdrop);
    font-family: "Montserrat", sans-serif;
  }
  .sheet {
    position: relative; width: 1200px; height: 912px;
    display: flex; align-items: center; justify-content: center; gap: 30px;
  }
  .card {
    position: relative; width: 560px; height: 320px;
    border-radius: 16px; overflow: hidden;
    background: var(--brand-blue);
    box-shadow: 0 4px 14px rgba(0,0,0,0.12);
  }
  /* Front */
  .card-front {
    display: flex; flex-direction: column; align-items: center; justify-content: center;
    color: var(--text-light);
  }
  .front-wordmark {
    display: flex; align-items: center; gap: 12px;
    font-weight: 700; font-size: 56px; letter-spacing: -1px; line-height: 1;
  }
  .wordmark-dot {
    width: 20px; height: 20px; border-radius: 50%;
    background: var(--text-light); flex: none;
  }
  .front-tagline {
    margin-top: 24px; font-size: 15px; font-weight: 400; letter-spacing: 0.3px;
  }
  /* Back */
  .back-shape { position: absolute; inset: 0; }
  .back-wordmark {
    position: absolute; top: 56px; right: 40px;
    display: flex; align-items: center; gap: 10px;
    color: var(--brand-blue);
    font-weight: 700; font-size: 40px; letter-spacing: -1px; line-height: 1;
  }
  .back-wordmark .wordmark-dot { width: 16px; height: 16px; background: var(--brand-blue); }
  .contact {
    position: absolute; left: 44px; top: 160px; color: var(--text-light);
  }
  .contact-name { font-weight: 700; font-size: 20px; line-height: 24px; color: var(--soft-blue); }
  .contact-title { font-size: 14px; line-height: 18px; margin-top: 1px; }
  .contact-rule { width: 32px; height: 1px; background: var(--soft-blue); margin: 8px 0 8px; }
  .contact-list { list-style: none; }
  .contact-item {
    display: flex; align-items: center; gap: 10px;
    font-size: 13px; line-height: 20px; margin-bottom: 5px;
  }
  .contact-item:last-child { margin-bottom: 0; }
  .contact-icon {
    width: 20px; height: 20px; border-radius: 50%;
    border: 1px solid var(--soft-blue);
    display: flex; align-items: center; justify-content: center; flex: none;
  }
  .contact-icon svg { width: 11px; height: 11px; }
</style>
</head>
<body>
<main class="sheet">
  <section class="card card-front" aria-label="Card front">
    <div class="front-wordmark"><span class="wordmark-dot"></span><span>Tarnwove</span></div>
    <p class="front-tagline">The Deck Judge’s Home Base</p>
  </section>

  <section class="card card-back" aria-label="Card back">
    <svg class="back-shape" viewBox="0 0 560 320" aria-hidden="true">
      <path d="M138,0 C178,180 330,238 560,182" fill="none" stroke="var(--soft-blue)" stroke-width="7"/>
      <path d="M150,0 C190,170 330,225 560,170 L560,0 Z" fill="var(--paper)"/>
    </svg>
    <div class="back-wordmark"><span class="wordmark-dot"></span><span>Tarnwove</span></div>
    <div class="contact">
      <p class="contact-name">Martin Oyelaran</p>
      <p class="contact-title">CEO &amp; Founder</p>
      <div class="contact-rule"></div>
      <ul class="contact-list">
        <li class="contact-item">
          <span class="contact-icon"><svg viewBox="0 0 24 24" fill="none" stroke="#9aaddc" stroke-width="2.2"><path d="M5 3h4l2 5-3 2a12 12 0 0 0 6 6l2-3 5 2v4a2 2 0 0 1-2 2A18 18 0 0 1 3 5a2 2 0 0 1 2-2z"/></svg></span>
          <span>(555) 201-4473</span>
        </li>
        <li class="contact-item">
          <span class="contact-icon"><svg viewBox="0 0 24 24" fill="none" stroke="#9aaddc" stroke-width="2.2"><rect x="3" y="5" width="18" height="14" rx="1"/><path d="M3 6l9 7 9-7"/></svg></span>
          <span>martin@tarnwove.com</span>
        </li>
        <li class="contact-item">
          <span class="contact-icon"><svg viewBox="0 0 24 24" fill="none" stroke="#9aaddc" stroke-width="2"><circle cx="12" cy="12" r="9"/><path d="M3 12h18M12 3c3 3 3 15 0 18M12 3c-3 3-3 15 0 18"/></svg></span>
          <span>www.tarnwove.com</span>
        </li>
      </ul>
    </div>
  </section>
</main>
</body>
</html>
```